SEO Agentur www.klickretter.de - Webseite soll neu designed werden (Start- und Unterseite)
Zielgruppe
Alle Infos sind auf der Seite www.klickretter.de enthalten.
Aufgabenstellung
Die Seite soll neu gestalltet werden. Wir möchten gerne ein wenig professioneller werden. Der Name der Seite zwingt uns allerdings ein gewisses Thema auf.
Die Aufgabe:
Ein professionelleres Design der Startseite und einer Unterseite. Die Programmierung machen wir selbst. Thema Suche und Helden muss bleiben aufgrund der URL.
Mit dem Gewinner würden wir dann auch geren jedes Element der Seite durchgehen und neu gestallten (separater Auftrag).
Das Blitzwolf Logo ist aufgrund des neuen Films auch gewaltiger und seriöser geworden. Vielleicht kann man daran anknüpfen. Ist aber keine Bedingung nur eine kleine Idee.
Wir werden alle Vorschläge ca. 50 Leuten vorstellen und dann den Vorschlag mit den meisten Stimmen wählen.

```html
<!DOCTYPE html>
<html lang="en">
<head>
<meta charset="utf-8">
<title>Klickretter – SEO Agency</title>
<link href="https://fonts.googleapis.com/css2?family=Ubuntu:wght@300;400;500&family=Ubuntu+Condensed&family=Roboto:wght@400;700&display=swap" rel="stylesheet">
<style>
:root{
  --blue:#0a88c8;
  --red:#e8302a;
  --text:#2d2d2d;
  --muted:#5a5a5a;
  --panel:#f5f3f3;
  --yellow:#f2c81e;
  --green:#58b87a;
  --pink:#c4488e;
  --footer:#bcdbe8;
  --bar:#3a98cf;
}
*{box-sizing:border-box;margin:0;padding:0}
html,body{width:901px;height:1200px;overflow:hidden;background:#fff}
body{position:relative;font-family:"Ubuntu",sans-serif;color:var(--text)}
.abs{position:absolute}

.site-header{position:absolute;left:0;top:0;width:901px;height:67px;border-bottom:2px solid var(--yellow);background:#fff}
.brand{position:absolute;left:118px;top:22px;display:flex;align-items:center;gap:6px;font-weight:500;font-size:15px;color:var(--red)}
.brand-mark{width:14px;height:14px;background:var(--yellow)}
.main-nav{position:absolute;top:0;left:317px;height:65px;display:flex;font-size:8.4px;font-weight:500}
.main-nav a{color:#333;text-decoration:none;line-height:63px;padding:0 6px}
.main-nav a.active{background:var(--blue);color:#fff;width:57px;text-align:center;margin-right:5px}
.main-nav .hl{color:var(--red)}

.hero{position:absolute;left:0;top:67px;width:901px;height:339px;background:linear-gradient(120deg,#cde7f0 0%,#bfe0ee 40%,#e6eef2 70%,#a9d2e4 100%)}
.callout{position:absolute;background:rgba(240,246,249,.82);display:flex;align-items:center}
.callout.one{left:120px;top:94px;width:322px;height:47px;border-left:3px solid var(--yellow);padding-left:20px;font-size:9px}
.callout.two{left:177px;top:142px;width:265px;height:47px;border-left:3px solid var(--green);justify-content:flex-end;padding-right:8px;font-size:12px}
.callout.three{left:233px;top:191px;width:209px;height:47px;border-left:3px solid var(--pink);justify-content:flex-end;padding-right:8px;font-size:14px}

.page-title{position:absolute;top:425px;left:0;width:901px;text-align:center;font-family:"Roboto",sans-serif;font-weight:700;font-size:24px;color:#1b1b1b}
.services{position:absolute;left:118px;top:466px;width:662px;height:206px;background:var(--panel);border-top:1px solid #e2e2e2}
.ribbon{position:absolute;left:177px;top:-1px;width:279px;height:21px;background:var(--red);color:#fff;font-family:"Roboto",sans-serif;font-size:10.5px;text-align:center;line-height:21px}
.service{position:absolute;width:200px}
.service .ico{position:absolute;left:0;top:0;width:45px;height:45px;border-radius:50%}
.service h3{position:absolute;left:54px;top:0;font-weight:400;font-size:9.5px;color:#333;white-space:nowrap}
.service p{position:absolute;left:55px;top:16px;width:140px;font-weight:300;font-size:6.2px;line-height:10px;color:var(--muted)}
.more{color:var(--red);font-style:italic}

.block-title{position:absolute;font-family:"Ubuntu Condensed",sans-serif;font-weight:400;font-size:14px;color:#1b1b1b}
.block-sub{position:absolute;font-size:7.3px;font-weight:300;color:var(--red)}
.block-body{position:absolute;font-size:6.1px;font-weight:300;line-height:10px;color:#333}

.step{position:absolute;width:160px}
.step .ico{position:absolute;left:0;top:0;width:42px;height:42px;border-radius:50%}
.step h4{position:absolute;left:47px;top:0;font-weight:400;font-size:7.6px}
.step p{position:absolute;left:47px;top:13px;width:108px;font-size:6.2px;line-height:10px;color:#222}
.step .rm{color:var(--red)}

.contact-panel{position:absolute;left:472px;top:775px;width:303px;height:192px;background:var(--panel)}
.field{position:absolute;height:22px;border:1px solid #d8d8d8;background:#fff;font-size:7px;font-weight:300;color:#777;padding:6px 5px}
.send{position:absolute;left:248px;top:163px;width:47px;height:22px;background:var(--red);color:#fff;font-size:8px;font-weight:500;text-align:center;line-height:22px}

.site-footer{position:absolute;left:0;top:990px;width:901px;height:190px;background:var(--footer)}
.f-head{position:absolute;top:12px;font-size:12px;color:var(--red)}
.f-sub{position:absolute;font-size:6.8px;color:#333}
.f-list{position:absolute;list-style:none;font-size:6.2px;line-height:13.5px;color:#333;letter-spacing:.2px}
.f-list li::before{content:"» "}
.f-item{position:absolute;left:129px;display:flex;gap:5px;font-size:6.2px;line-height:9px;color:#333}
.f-item i{display:block;width:13px;height:13px;border:1px solid #9a6ab0;border-radius:50%;margin-top:1px}
.bottom-bar{position:absolute;left:0;top:1180px;width:901px;height:20px;background:var(--bar);color:#fff;font-size:6.6px;line-height:20px}
</style>
</head>
<body>

<header class="site-header">
  <div class="brand"><span class="brand-mark"></span>Klickretter</div>
  <nav class="main-nav">
    <a class="active" href="#">Home</a>
    <a href="#">Expiration</a>
    <a href="#">Benefits</a>
    <a href="#">Our Services</a>
    <a href="#"><span class="hl">100%</span> money-back guarantee</a>
    <a href="#">Info</a>
    <a href="#">Blog</a>
    <a href="#">Contact</a>
  </nav>
</header>

<section class="hero" role="img" aria-label="Photo of hands typing on a laptop showing an analytics dashboard">
  <div class="callout one">We are the right person when it comes to optimizing your website!</div>
  <div class="callout two">Our years of experience!</div>
  <div class="callout three">GUARANTEED! Talk to us</div>
</section>

<h1 class="page-title">SEO AGENCY CLICK RESCUE</h1>

<section class="services">
  <div class="ribbon">success-based and with <b>100%</b> money back guarantee</div>

  <div class="service" style="left:9px;top:50px">
    <svg class="ico" viewBox="0 0 45 45"><circle cx="22.5" cy="22.5" r="22.5" fill="#a9b96b"/><circle cx="20" cy="19" r="8" fill="none" stroke="#fff" stroke-width="2"/><line x1="26" y1="25" x2="32" y2="31" stroke="#fff" stroke-width="3"/></svg>
    <h3>Search Engine Optimization</h3>
    <p>Around 40% of users click on search engines like Findr, Seekly and Lookup on the Inter side that will be ranked <span class="more">read more...</span></p>
  </div>
  <div class="service" style="left:240px;top:50px">
    <svg class="ico" viewBox="0 0 45 45"><circle cx="22.5" cy="22.5" r="22.5" fill="#2b9ccc"/><rect x="15" y="11" width="15" height="22" fill="none" stroke="#fff" stroke-width="1.6"/><line x1="18" y1="16" x2="27" y2="16" stroke="#fff"/><line x1="18" y1="19" x2="27" y2="19" stroke="#fff"/><circle cx="22.5" cy="27" r="2.5" fill="none" stroke="#fff"/></svg>
    <h3 style="left:56px">Search engine advertising</h3>
    <p style="left:57px">Especially for young companies is the topic of search engine advertising is an important part of the online marketing mix. <span class="more">read more...</span></p>
  </div>
  <div class="service" style="left:460px;top:50px">
    <svg class="ico" viewBox="0 0 45 45"><circle cx="22.5" cy="22.5" r="22.5" fill="#a2805f"/><rect x="11" y="13" width="23" height="15" fill="none" stroke="#fff" stroke-width="1.6"/><line x1="22.5" y1="28" x2="22.5" y2="32" stroke="#fff" stroke-width="1.6"/><line x1="17" y1="32" x2="28" y2="32" stroke="#fff" stroke-width="1.6"/><line x1="19" y1="24" x2="28" y2="15" stroke="#fff" stroke-width="1.6"/></svg>
    <h3 style="left:57px">Website creation</h3>
    <p style="left:58px;width:134px">We create your website from A to Z! Whether custom design your website professionally prepared texts or contact <span class="more">read more...</span></p>
  </div>

  <div class="service" style="left:9px;top:134px">
    <svg class="ico" viewBox="0 0 45 45"><circle cx="22.5" cy="22.5" r="22.5" fill="#d6bf33"/><path d="M13 27a6 6 0 0 1 2-11 8 8 0 0 1 15 0 6 6 0 0 1 2 11z" fill="none" stroke="#fff" stroke-width="1.6"/></svg>
    <h3>Social Media SEO</h3>
    <p>Social Media is called the digital medium, which moves the user and sustainable impressed.In recent years, <span class="more">read more...</span></p>
  </div>
  <div class="service" style="left:240px;top:134px">
    <svg class="ico" viewBox="0 0 45 45"><circle cx="22.5" cy="22.5" r="22.5" fill="#9a70ad"/><path d="M22.5 34c-6-6-9-10-9-14a9 9 0 0 1 18 0c0 4-3 8-9 14z" fill="none" stroke="#fff" stroke-width="1.6"/><path d="M22.5 15l1.6 3.3 3.6.5-2.6 2.5.6 3.6-3.2-1.7-3.2 1.7.6-3.6-2.6-2.5 3.6-.5z" fill="#fff"/></svg>
    <h3 style="left:56px">Findr Penalty</h3>
    <p style="left:57px">If your website has a massive loss of visibility and thus also of traffic, you have very likely get a manual punishment <span class="more">read more...</span></p>
  </div>
  <div class="service" style="left:460px;top:134px">
    <svg class="ico" viewBox="0 0 45 45"><circle cx="22.5" cy="22.5" r="22.5" fill="#ee6a5e"/><rect x="12" y="13" width="21" height="19" fill="none" stroke="#fff" stroke-width="1.6"/><path d="M19 18v10l8-5z" fill="#fff"/></svg>
    <h3 style="left:57px">Explanatory videos</h3>
    <p style="left:58px;width:134px">The click rescuers produce videos for the display of products, websites, software or services. <span class="more">read more...</span></p>
  </div>
</section>

<h2 class="block-title" style="left:118px;top:690px">WHY CHOOSE US?</h2>
<div class="block-sub" style="left:118px;top:709px">More customers through a better online performance</div>
<p class="block-body" style="left:118px;top:726px;width:310px">We are your ideal partner for performance marketing! We offer many years of expertise, develop and implement successful online marketing campaigns for your business to. Through our experience and our know-how your site is positioned as Findr &amp; Co.</p>

<h2 class="block-title" style="left:472px;top:690px">100% MONEY BACK GUARANTEE</h2>
<div class="block-sub" style="left:472px;top:709px">Within 6 months among the top 10 or you get your money back.</div>
<p class="block-body" style="left:472px;top:726px;width:290px">We have one goal: your business at # 1 in the search results of Findr &amp; Co. bring. We know our business, so we have a 100% money-back-guarantee on our service offer, contrary to many competitors.</p>

<h2 class="block-title" style="left:118px;top:780px">THE SEQUENCE</h2>
<div class="block-sub" style="left:118px;top:799px">4 Steps to Success</div>

<div class="step" style="left:118px;top:822px">
  <svg class="ico" viewBox="0 0 42 42"><circle cx="21" cy="21" r="21" fill="#2b9ccc"/><rect x="9" y="11" width="24" height="16" fill="none" stroke="#fff" stroke-width="1.5"/><path d="M12 24l4-5 3 3 4-6 3 4 4-5" fill="none" stroke="#fff" stroke-width="1.3"/></svg>
  <h4 style="color:#2b9ccc">Keyword analysis</h4>
  <p>After detailed contact request we perform automatically by an analysis <span class="rm">read more</span></p>
</div>
<div class="step" style="left:281px;top:822px">
  <svg class="ico" viewBox="0 0 42 42"><circle cx="21" cy="21" r="21" fill="#e9474a"/><circle cx="21" cy="16" r="4" fill="#fff"/><path d="M13 30a8 7 0 0 1 16 0z" fill="#fff"/></svg>
  <h4 style="color:var(--red)">Offer meeting</h4>
  <p>As part of the offer meeting we will explain in detail the benefits and the value <span class="rm">read more</span></p>
</div>
<div class="step" style="left:118px;top:906px">
  <svg class="ico" viewBox="0 0 42 42"><circle cx="21" cy="21" r="21" fill="#8e5a8c"/><rect x="12" y="12" width="18" height="18" fill="none" stroke="#fff" stroke-width="1.5"/><line x1="15" y1="17" x2="27" y2="17" stroke="#fff"/><line x1="15" y1="21" x2="27" y2="21" stroke="#fff"/><line x1="15" y1="25" x2="23" y2="25" stroke="#fff"/></svg>
  <h4 style="color:#8e5a8c">Quotation</h4>
  <p>Now we are on the course! Based on the selected and optimal for your websit <span class="rm">read more</span></p>
</div>
<div class="step" style="left:281px;top:906px">
  <svg class="ico" viewBox="0 0 42 42"><circle cx="21" cy="21" r="21" fill="#8cb43c"/><rect x="10" y="15" width="22" height="14" fill="none" stroke="#fff" stroke-width="1.5"/><path d="M17 15v-3h8v3M10 20l11 4 11-4" fill="none" stroke="#fff" stroke-width="1.3"/></svg>
  <h4 style="color:#8cb43c">Contract</h4>
  <p>After we have received the signed service agreement, we immedi-ately begin <span class="rm">read more</span></p>
</div>

<section class="contact-panel">
  <h2 class="block-title" style="left:7px;top:13px">CONTACT US</h2>
  <div class="block-sub" style="left:7px;top:33px">Or Call Us (0541) 555 019 27</div>
  <div class="field" style="left:9px;top:44px;width:140px">Name</div>
  <div class="field" style="left:156px;top:44px;width:139px">Phone</div>
  <div class="field" style="left:9px;top:72px;width:140px">E-mail</div>
  <div class="field" style="left:156px;top:72px;width:139px">Website</div>
  <div class="field" style="left:9px;top:100px;width:286px;height:50px">Message</div>
  <div class="send">SEND</div>
</section>

<footer class="site-footer">
  <div class="f-head" style="left:129px">CONTACT</div>
  <div class="f-sub" style="left:129px;top:34px">Klickretter.de GbR</div>
  <div class="f-item" style="top:54px"><i></i><span>Klickretter.de GbR<br>Lindenweg 12<br>49080 Feldstadt</span></div>
  <div class="f-item" style="top:85px"><i style="border-color:#e8807a"></i><span>Imprint<br>Contact Form</span></div>
  <div class="f-item" style="top:110px"><i style="border-color:#3a98cf"></i><span>Hotline 0541 - 555 019 27<br>We are waiting for your call</span></div>

  <div class="f-head" style="left:286px">SITEMAP</div>
  <div class="f-sub" style="left:286px;top:34px">Menu</div>
  <ul class="f-list" style="left:286px;top:50px">
    <li>About Us</li><li>Benefits</li><li>How it works?</li><li>100% money-back guarantee</li><li>Contact</li><li>Search Engine Optimization</li><li>Website creation</li><li>Search engine advertising</li><li>Social SEO</li><li>Blog</li>
  </ul>

  <div class="f-sub" style="left:444px;top:34px">Search Engine Optimization</div>
  <ul class="f-list" style="left:444px;top:50px">
    <li>SEO Agency</li><li>SEO Marketing</li><li>SEO Sales</li><li>SEO Agency</li><li>Success based SEO Agency</li>
  </ul>
  <div class="f-sub" style="left:444px;top:129px">Websites</div>
  <ul class="f-list" style="left:444px;top:145px">
    <li>Website development</li><li>Can create homepage</li>
  </ul>

  <div class="f-sub" style="left:585px;top:34px">Search engine advertising</div>
  <ul class="f-list" style="left:585px;top:50px">
    <li>AdLinks Agency</li><li>Findr AdLinks</li><li>SEA Agency</li><li>SEM Agency</li>
  </ul>
  <div class="f-sub" style="left:585px;top:129px">Findr penalizing</div>
  <ul class="f-list" style="left:585px;top:145px">
    <li>Findr penalizing</li><li>Findr Penalty</li>
  </ul>

  <div class="f-sub" style="left:708px;top:34px">Explanatory videos</div>
  <ul class="f-list" style="left:708px;top:50px">
    <li>Explanatory videos</li><li>Explain Movies</li><li>Product Videos</li>
  </ul>
</footer>

<div class="bottom-bar">
  <span class="abs" style="left:124px">© 2003-2014 klickretter.de All Rights Reserved.</span>
  <span class="abs" style="right:122px">Imprint &nbsp;/&nbsp; Contact</span>
</div>

</body>
</html>
```